Logistics Website Design

See website https://tqfreightglobal.com for theme and color details. Need the site to be re-done and reflect some of the designs shown in this list here: https://pixelvane.com/tags/logistics-company-website

Target Market(s)

Logistics & Transportation

Industry/Entity Type

Logistics and Supply Chain

Coding

Number of Pages Required

5+ page

Requirements
Must have
• Colors must match theme of logo. Looking for a sleek, interactive design.

```html
<!DOCTYPE html>
<html lang="en">
<head>
<meta charset="utf-8">
<title>TQ Freight Global</title>
<link href="https://fonts.googleapis.com/css2?family=Bebas+Neue&family=Lato:wght@400;700;900&family=Roboto:wght@400;500&display=swap" rel="stylesheet">
<style>
:root{
  --orange:#ee7f57;
  --orange-soft:#fbe3d8;
  --dark:#2a0f08;
  --ink:#141414;
  --muted:#555;
  --sky:#e3f3fa;
  --footer:#1f0e0a;
  --white:#fff;
}
*{box-sizing:border-box;margin:0;padding:0}
html,body{width:1200px;height:4272px;overflow:hidden;background:var(--white);font-family:"Lato",sans-serif;color:var(--ink)}
.page{position:relative;width:1200px;height:4272px}
.abs{position:absolute}
.display{font-family:"Bebas Neue",sans-serif;font-weight:400;line-height:1}
.accent{color:var(--orange)}
.btn{position:absolute;display:flex;align-items:center;justify-content:center;height:42px;border-radius:21px;background:var(--dark);color:var(--white);border:3px solid var(--orange);font:900 13px "Lato",sans-serif;letter-spacing:.3px}
.btn.orange{background:var(--orange);border-color:#f6a284}
.eyebrow{position:absolute;font:900 20px "Lato",sans-serif;color:var(--dark)}

/* hero */
.nav-left{left:112px;top:64px;width:403px;height:53px;background:var(--white);border-radius:27px;display:flex;align-items:center;font:400 14px "Lato",sans-serif}
.nav-left .active{background:var(--orange);color:var(--white);height:53px;border-radius:27px 0 0 27px;padding:0 22px;display:flex;align-items:center;font-weight:700}
.nav-left span{margin-left:20px}
.nav-right{left:680px;top:64px;width:413px;height:53px;background:var(--white);border-radius:27px;font-size:14px}
.nav-right .quote{position:absolute;left:26px;top:18px}
.nav-right .btn{right:4px;top:4px;width:124px;height:45px;font-size:12px}
.brand{left:538px;top:30px;width:124px;height:124px;border-radius:50%;background:var(--dark);border:4px solid var(--orange);display:flex;align-items:center;justify-content:center;color:var(--white);font:900 15px "Lato",sans-serif;text-align:center;line-height:1.2}
.hero-title{left:118px;top:188px;font-size:118px;color:var(--white);letter-spacing:1px;transform:skewX(-10deg);transform-origin:left bottom}
.hero-sub{left:112px;top:553px;color:var(--white);font:700 19px "Lato",sans-serif}
/* services */
.svc-title{left:111px;top:945px;font-size:54px;line-height:61px}
.svc-text{left:112px;top:1136px;width:290px;font:400 15px/28px "Lato",sans-serif;color:var(--muted)}
.card{position:absolute;background:var(--white);box-shadow:0 4px 16px rgba(0,0,0,.14)}
.flatbed{left:439px;top:913px;width:340px;height:371px;background:linear-gradient(180deg,#4ea3d8 0%,#a8cde6 45%,#c23a36 70%,#6d6c6c 100%)}
.flatbed h3{position:absolute;left:42px;top:30px;font-size:40px;line-height:50px;color:var(--white)}
.dryvan{left:799px;top:913px;width:341px;height:371px}
.dryvan h3{position:absolute;left:24px;top:33px;font-size:30px;color:var(--dark)}
.dryvan p{position:absolute;left:24px;top:78px;width:300px;font:400 13px/24px "Roboto",sans-serif;color:var(--muted)}
.dryvan .photo{position:absolute;left:10px;top:178px;width:321px;height:180px;border-radius:6px;background:linear-gradient(180deg,#8fb0cf 0%,#c9b59a 55%,#5c5a58 100%)}
/* about */
.about{left:21px;top:1395px;width:1157px;height:416px;background:var(--sky);border-radius:14px}
.about .eyebrow{left:0;width:100%;text-align:center;top:76px}
.about h2{position:absolute;left:0;width:100%;text-align:center;top:118px;font-size:54px}
.about p{position:absolute;left:145px;width:867px;top:192px;text-align:center;font:400 14px/28px "Roboto",sans-serif;color:var(--muted)}
/* industries */
.ind-head{left:0;width:1200px;text-align:center}
.ind-card{position:absolute;top:2071px;width:191px;height:229px;background:var(--white);box-shadow:0 3px 12px rgba(0,0,0,.13);text-align:center;font:400 19px/28px "Roboto",sans-serif}
.ind-card .icon{width:70px;height:70px;border-radius:50%;background:var(--orange-soft);margin:29px auto 20px;display:flex;align-items:center;justify-content:center}
.ind-card.on .icon{background:var(--orange)}
/* contact banner */
.banner{left:20px;top:2403px;width:1156px;height:576px;border-radius:14px;background:linear-gradient(90deg,#2d6fb0 0%,#b5472f 30%,#9ec8e4 60%,#c55a3c 85%,#8d3326 100%)}
.panel{left:111px;top:2447px;width:522px;height:456px;background:rgba(255,255,255,.9)}
.panel h2{position:absolute;left:42px;top:96px;font-size:58px;line-height:74px}
.panel p{position:absolute;left:42px;top:240px;width:440px;font:400 25px/40px "Lato",sans-serif;color:#555}
/* leadership */
.leader-photo{left:111px;top:3084px;width:444px;height:426px;background:linear-gradient(160deg,#9fc7e6 0%,#d9e7f1 40%,#26406b 75%,#c25a35 100%)}
.lead-title{left:640px;top:3100px;font-size:56px}
.lead-sub{left:640px;top:3162px;font-size:29px;color:var(--dark)}
.lead-text{left:640px;top:3212px;width:450px;font:400 13px/27.4px "Roboto",sans-serif;color:var(--muted);text-align:justify}
/* footer */
.foot-title{left:110px;top:3752px;color:var(--white);font:900 25px/35px "Lato",sans-serif}
.email{left:565px;top:3758px;width:381px;height:46px;border-radius:23px;background:var(--white);font:400 13px "Lato",sans-serif;color:#666;padding:16px 26px}
.foot-brand{left:152px;top:3905px;width:200px;height:200px;border-radius:50%;background:var(--footer);border:5px solid var(--orange);display:flex;align-items:center;justify-content:center;text-align:center;color:var(--orange);font:900 24px/1.2 "Lato",sans-serif}
.social{top:4115px;width:29px;height:29px;border-radius:50%;background:var(--white)}
.col h4{font:400 23px "Roboto",sans-serif;color:var(--orange);margin-bottom:14px}
.col li{list-style:none;font:400 14px/31px "Lato",sans-serif;color:var(--white)}
.contact li{display:flex;align-items:center;gap:20px;line-height:52px}
.rule{left:111px;top:4184px;width:987px;height:1px;background:#6b5248}
.legal{top:4205px;font:400 11px "Lato",sans-serif;color:var(--white)}
</style>
</head>
<body>
<div class="page">

  <!-- Hero -->
  <svg class="abs" style="left:0;top:0" width="1200" height="830" viewBox="0 0 1200 830">
    <defs>
      <linearGradient id="heroFill" x1="0" y1="0" x2="1" y2="1">
        <stop offset="0" stop-color="#1e2f45"/><stop offset=".45" stop-color="#6b7f96"/><stop offset=".75" stop-color="#9a4a3a"/><stop offset="1" stop-color="#3b3a3d"/>
      </linearGradient>
    </defs>
    <path role="img" aria-label="Photo of a white semi truck driving through a container port" d="M15 15 H1185 V663 Q600 920 15 663 Z" fill="url(#heroFill)"/>
    <path d="M15 668 Q600 935 1185 668" fill="none" stroke="var(--orange)" stroke-width="9"/>
  </svg>
  <div class="abs nav-left"><div class="active">Home</div><span>Services</span><span>Industries</span><span style="margin-left:32px">About Us</span></div>
  <div class="abs brand">TQ FREIGHT<br>GLOBAL</div>
  <div class="abs nav-right"><span class="quote">Request a Quote</span><div class="btn">CONTACT US</div></div>
  <h1 class="abs display hero-title">DELIVERING<br>STRENGTH IN<br>EVERY MILE</h1>
  <p class="abs hero-sub">Secure and reliable transportation for all your cargo needs.</p>
  <div class="btn orange" style="left:112px;top:593px;width:162px">REQUEST A QUOTE</div>

  <!-- Services -->
  <div class="eyebrow" style="left:112px;top:908px">SERVICES</div>
  <h2 class="abs display svc-title">FAST <span class="accent">PRECISION<br>DELIVERY</span> FOR<br>EVERYONE</h2>
  <p class="abs svc-text">End-to-end logistics solutions tailored for oversized, specialized, and time-critical shipments.</p>
  <div class="btn" style="left:112px;top:1246px;width:123px">VIEW ALL</div>
  <div class="card flatbed" role="img" aria-label="Photo of a red flatbed truck hauling lumber"><h3 class="display">FLATBED<br>TRANSPORTATION</h3></div>
  <div class="card dryvan">
    <h3 class="display">DRY VAN TRANSPORTATION</h3>
    <p>TQ Freight Global delivers enclosed freight solutions designed to protect your cargo and keep your logistics running smoothly.</p>
    <div class="photo" role="img" aria-label="Photo of a white dry van truck on a desert highway"></div>
  </div>

  <!-- About -->
  <section class="abs about">
    <div class="eyebrow">ABOUT US</div>
    <h2 class="display">KEEPING YOUR <span class="accent">SUPPLY CHAIN MOVING</span></h2>
    <p>We deliver a comprehensive range of open-deck and specialized transportation services—including flatbed, step deck, heavy haul, and over-dimensional freight solutions. Backed by years of experience, a trusted nationwide carrier network, and a strong safety-first culture, we provide reliable, adaptable logistics support built around the unique requirements of every load.</p>
    <div class="btn" style="left:517px;top:303px;width:124px">READ MORE</div>
  </section>

  <!-- Industries -->
  <div class="eyebrow ind-head" style="top:1920px">INDUSTRIES</div>
  <h2 class="abs display ind-head" style="top:1962px;font-size:54px">WHO <span class="accent">WE SERVE</span></h2>
  <div class="ind-card" style="left:111px"><div class="icon"><svg width="30" height="30" viewBox="0 0 30 30"><path d="M5 14h20l-2 12H7z M9 14l4-8 M17 6l4 8" fill="none" stroke="var(--orange)" stroke-width="2.5"/></svg></div>FOOD &amp;<br>BEVERAGE</div>
  <div class="ind-card" style="left:310px"><div class="icon"><svg width="30" height="30" viewBox="0 0 30 30"><path d="M5 12h20v14H5z M3 12l3-7h18l3 7 M12 26v-8h6v8" fill="none" stroke="var(--orange)" stroke-width="2.5"/></svg></div>E-Commerce &amp;<br>RETAIL</div>
  <div class="ind-card on" style="left:508px"><div class="icon"><svg width="30" height="30" viewBox="0 0 30 30"><circle cx="15" cy="11" r="6" fill="none" stroke="#fff" stroke-width="2.5"/><path d="M4 24h22" stroke="#fff" stroke-width="3"/></svg></div>Manufacturing</div>
  <div class="ind-card" style="left:707px"><div class="icon"><svg width="30" height="30" viewBox="0 0 30 30"><rect x="8" y="9" width="14" height="17" rx="2" fill="none" stroke="var(--orange)" stroke-width="2.5"/><path d="M15 13v8 M11 17h8 M10 4h10" stroke="var(--orange)" stroke-width="2.5"/></svg></div>Pharma &amp;<br>Healthcare</div>
  <div class="ind-card" style="left:905px"><div class="icon"><svg width="30" height="30" viewBox="0 0 30 30"><path d="M15 4l9 4v7c0 6-4 10-9 12-5-2-9-6-9-12V8z" fill="none" stroke="var(--orange)" stroke-width="2.5"/></svg></div>Government<br>Secured Freight</div>

  <!-- Contact banner -->
  <div class="abs banner" role="img" aria-label="Photo of a white truck among stacked shipping containers"></div>
  <div class="abs panel">
    <div class="eyebrow" style="left:45px;top:36px">CONTACT US</div>
    <h2 class="display">LET'S MOVE <span class="accent">YOUR<br>BUSINESS FORWARD</span></h2>
    <p>Let's discuss your logistics needs and how we can help your business thrive</p>
    <div class="btn" style="left:41px;top:356px;width:124px">CONTACT US</div>
  </div>

  <!-- Leadership -->
  <div class="abs leader-photo" role="img" aria-label="Portrait of the director of agency sales in a blue suit at a freight yard"></div>
  <h2 class="abs display lead-title">LEADERSHIP <span class="accent">TEAM</span></h2>
  <h3 class="abs display lead-sub">DARREN OKAFOR, DIRECTOR OF AGENCY SALES</h3>
  <p class="abs lead-text">Darren is a driven entrepreneur and the Founder of BRIGHTLANE GOODS®, a rapidly growing e-commerce and wholesale operation connecting fitness brands, gyms, and buyers worldwide. A Hillcrest State alumnus, Okafor earned national recognition as a member of Ledger Weekly's "Rising 1,000"—an honor awarded to standout emerging entrepreneurs from over 200,000+ applicants. Built from the ground up with no outside advantages, his journey reflects resilience, grit, and a relentless commitment to innovation in the fitness and e-commerce industries.</p>
  <div class="btn" style="left:640px;top:3456px;width:124px">READ MORE</div>

  <!-- Footer -->
  <svg class="abs" style="left:0;top:3590px" width="1200" height="682" viewBox="0 0 1200 682">
    <path d="M15 170 Q600 -60 1185 170 V682 H15 Z" fill="var(--footer)"/>
    <path d="M15 163 Q600 -72 1185 163" fill="none" stroke="var(--orange)" stroke-width="9"/>
  </svg>
  <p class="abs foot-title">SIGNUP TO RECEIVE OUR OFFER,<br>AND STAY UPTO DATE</p>
  <div class="abs email">Enter email address</div>
  <div class="btn" style="left:959px;top:3759px;width:121px;height:44px">SUBSCRIBE</div>
  <div class="abs foot-brand">TQ FREIGHT<br>GLOBAL</div>
  <div class="abs social" style="left:169px;background:var(--orange)"></div>
  <div class="abs social" style="left:208px"></div>
  <div class="abs social" style="left:247px"></div>
  <div class="abs social" style="left:288px"></div>
  <div class="abs col" style="left:496px;top:3880px"><h4>Quick Links</h4><ul><li>Home</li><li>Services</li><li>Industries</li><li>About Us</li><li>Request a Quote</li><li>Contact Us</li></ul></div>
  <div class="abs col" style="left:694px;top:3878px"><h4>Services</h4><ul><li>Flatbed</li><li>Step Deck</li><li>Dry Van</li><li>Heavy Haul</li></ul></div>
  <div class="abs col contact" style="left:891px;top:3878px"><h4>Contact Info</h4><ul>
    <li><svg width="20" height="22" viewBox="0 0 20 22"><path d="M10 1a7 7 0 0 0-7 7c0 5 7 13 7 13s7-8 7-13a7 7 0 0 0-7-7z" fill="#fff"/><circle cx="10" cy="8" r="2.6" fill="var(--footer)"/></svg>Harbor Way,USA-582031</li>
    <li><svg width="20" height="20" viewBox="0 0 20 20"><circle cx="10" cy="10" r="10" fill="#fff"/><path d="M6 5l2 0 1 3-1.5 1a7 7 0 0 0 3.5 3.5l1-1.5 3 1v2c-5 1-10-4-9-9z" fill="var(--footer)"/></svg>+1 555 010 4400</li>
    <li><svg width="20" height="16" viewBox="0 0 20 16"><rect width="20" height="16" rx="3" fill="#fff"/><path d="M3 4l7 5 7-5" fill="none" stroke="var(--footer)" stroke-width="2"/></svg>info@tqfreightglobal.com</li>
  </ul></div>
  <div class="abs rule"></div>
  <p class="abs legal" style="left:114px">©2026 © TQ Freight Global .All Rights Reserved</p>
  <p class="abs legal" style="left:894px">Privacy Policy &nbsp; | &nbsp;Terms &amp; Conditions</p>
</div>
</body>
</html>
```